Website art for a private investigator.

The purposed graphic is for a business website ( brellwick.com ). The business name is “Harrowgate & Associates ltd.” This firm is a private investigation agency. The purposed graphic will be placed in the upper most main area of the main page of the website. If you look at the website now there is no graphic.

I have an idea of what I am looking for. I imagine a graphic depicting a contemporary private investigator walking through a dark alley searching for some unknown item. This is symbolic of private investigators hired to find information for people who their selfs do not have the know how nor could they handle the complexity and high stress environment. When I say contemporary I am referring to todays private investigators typically highly educated and well dressed.

Target Market(s)

People who need a private investigator

Industry/Entity Type

Business

Requirements
Must have
• match website; I have an idea of what I am looking for. I imagine a graphic depicting a contemporary private investigator walking through a dark alley searching for some unknown item. This is symbolic of private investigators hired to find information for people who their selfs do not have the know how nor could they handle the complexity and high stress environment. When I say contemporary I am referring to todays private investigators typically highly educated and well dressed.
Should not have
• Everyone please understand, I am not looking for a new website. I am only looking for the image. If you have submitted a design and its displayed on another website other than mine. I will not select your design. I am sorry for being harsh, but I asked for the image to match my website.

```html
<!DOCTYPE html>
<html lang="en">
<head>
<meta charset="utf-8">
<title>Brellwick — Private Investigations</title>
<link rel="stylesheet" href="https://fonts.googleapis.com/css2?family=Open+Sans:ital,wght@0,400;0,600;0,700;1,400;1,700;1,800&display=swap">
<style>
  :root {
    --page: #151515;
    --hero-top: #0e0e0e;
    --hero-bottom: #262626;
    --red: #b00f0f;
    --red-bright: #e0201c;
    --panel: #2a2a2a;
    --panel-edge: #333;
    --text: #f2f2f2;
    --muted: #9c9c9c;
    --dim: #6c6c6c;
    --accent: #3fa6dc;
    --nav: #171717;
    --nav-line: #2e2e2e;
  }
  * { box-sizing: border-box; margin: 0; padding: 0; }
  html, body { width: 1076px; height: 1200px; overflow: hidden; }
  body {
    background: var(--page);
    font-family: "Open Sans", Arial, sans-serif;
    color: var(--muted);
    position: relative;
  }
  .hero-band {
    position: absolute; left: 0; top: 0; width: 1076px; height: 547px;
    background: linear-gradient(var(--hero-top), var(--hero-bottom));
    border-bottom: 1px solid #2c2c2c;
  }
  .site-header { position: absolute; left: 144px; top: 14px; width: 789px; height: 70px; }
  .brand { position: absolute; left: 8px; top: 30px; display: flex; align-items: center; gap: 8px; }
  .brand-mark { width: 14px; height: 14px; background: var(--red); }
  .brand-name { color: var(--text); font-size: 27px; font-weight: 400; letter-spacing: -0.5px; }
  .social { position: absolute; right: 0; top: 10px; display: flex; gap: 10px; }
  .social span { width: 11px; height: 11px; border-radius: 50%; background: #e8e8e8; display: block; }
  .tollfree { position: absolute; right: 0; top: 34px; font-size: 15px; color: var(--text); }
  .tollfree strong { color: var(--red-bright); font-weight: 600; margin-left: 6px; font-size: 16px; }
  .main-nav {
    position: absolute; left: 144px; top: 92px; width: 789px; height: 38px;
    display: flex; background: var(--nav); border: 1px solid var(--nav-line);
  }
  .main-nav a {
    color: var(--text); text-decoration: none; font-size: 14px;
    display: flex; align-items: center; justify-content: center;
    border-right: 1px solid var(--nav-line);
  }
  .main-nav a:last-child { border-right: 0; }
  .main-nav a.active { background: var(--red); }
  .slider {
    position: absolute; left: 144px; top: 137px; width: 789px; height: 360px;
    box-shadow: 0 24px 28px rgba(0,0,0,.7);
  }
  .slide-photo {
    width: 100%; height: 100%;
    background: radial-gradient(ellipse at 62% 30%, #8a7a66 0%, #4a4036 30%, #1e1a16 65%, #0c0a09 100%);
  }
  .slide-arrow {
    position: absolute; top: 155px; width: 40px; height: 48px; background: rgba(0,0,0,.45);
    display: flex; align-items: center; justify-content: center;
  }
  .slide-arrow.prev { left: 0; }
  .slide-arrow.next { right: 0; }
  .slide-caption {
    position: absolute; left: 0; bottom: 0; width: 100%; height: 52px;
    background: rgba(0,0,0,.55); color: var(--text);
    font-style: italic; font-weight: 800; font-size: 22px;
    padding: 12px 24px; letter-spacing: 0.2px;
  }
  .welcome { position: absolute; left: 144px; top: 584px; width: 560px; }
  .welcome h1 { font-size: 22px; font-weight: 400; color: var(--text); margin-bottom: 10px; }
  .welcome p { font-size: 10.6px; line-height: 16px; }
  .client-login {
    position: absolute; left: 728px; top: 595px; width: 203px; height: 128px;
    background: #242424; border-radius: 6px; padding: 7px 12px;
  }
  .client-login h2 { color: var(--text); font-size: 18px; font-weight: 600; margin-bottom: 6px; }
  .client-login .field {
    width: 164px; height: 21px; margin-left: 16px; margin-bottom: 5px;
    background: #f3f3f3; border-radius: 3px; font-size: 9px; color: #888; padding: 4px 10px;
  }
  .client-login .btn {
    margin-left: 16px; margin-top: 4px; display: inline-block; background: var(--red);
    color: #fff; font-size: 11px; font-weight: 600; padding: 3px 12px;
  }
  .info-panel {
    position: absolute; left: 144px; top: 756px; width: 786px; height: 371px;
    background: var(--panel); border: 1px solid var(--panel-edge);
  }
  .info-col { position: absolute; top: 32px; }
  .info-col h3 { color: var(--text); font-size: 16px; font-weight: 600; margin-bottom: 10px; }
  .info-col p { font-size: 11.2px; line-height: 16px; }
  .col-do { left: 26px; width: 230px; }
  .col-charge { left: 282px; width: 230px; }
  .col-clients { left: 546px; width: 210px; }
  .read-more {
    position: absolute; top: 313px; background: var(--red); color: #fff;
    font-size: 9.5px; padding: 2px 6px;
  }
  .col-do + .read-more, .rm-do { left: 22px; }
  .rm-charge { left: 282px; }
  .quote { font-style: italic; font-size: 10.4px; line-height: 15px; color: var(--text); }
  .quote-author { text-align: right; color: var(--accent); font-size: 15px; margin-top: 10px; }
  .consult {
    margin-top: 12px; width: 205px; height: 100px; background: #8d8d8d;
    text-align: center; color: #111; font-weight: 700; padding-top: 13px;
  }
  .consult .label { font-size: 17px; line-height: 21px; }
  .consult .phone { font-size: 25px; color: #fff; margin-top: 3px; }
  .site-footer { position: absolute; left: 144px; top: 1158px; width: 789px; }
  .footer-nav { font-size: 10px; color: var(--dim); }
  .footer-social { position: absolute; right: 10px; top: -16px; display: flex; gap: 12px; }
  .footer-social span { width: 10px; height: 10px; border-radius: 50%; background: #444; display: block; }
  .copyright { position: absolute; right: 10px; top: 8px; font-size: 10px; color: var(--dim); }
  .copyright b { font-weight: 400; color: #8a8a8a; font-size: 13px; }
</style>
</head>
<body>
  <div class="hero-band"></div>

  <header class="site-header">
    <div class="brand"><span class="brand-mark"></span><span class="brand-name">Brellwick</span></div>
    <div class="social"><span></span><span></span><span></span><span></span></div>
    <div class="tollfree">Call Toll-Free: <strong>(555) 014-2276</strong></div>
  </header>

  <nav class="main-nav">
    <a class="active" style="width:117px">Home</a>
    <a style="width:119px">About Us</a>
    <a style="width:106px">Main</a>
    <a style="width:218px">Investigations &amp; Analysis</a>
    <a style="width:105px">News</a>
    <a style="flex:1">Contacts</a>
  </nav>

  <section class="slider">
    <div class="slide-photo" role="img" aria-label="Investigator with a flashlight searching a dark, smoky industrial ruin"></div>
    <div class="slide-arrow prev"><svg width="10" height="24" viewBox="0 0 10 24"><path d="M9 1 L1 12 L9 23" stroke="#aaa" fill="none" stroke-width="1.5"/></svg></div>
    <div class="slide-arrow next"><svg width="10" height="24" viewBox="0 0 10 24"><path d="M1 1 L9 12 L1 23" stroke="#aaa" fill="none" stroke-width="1.5"/></svg></div>
    <div class="slide-caption">A BITTER TRUTH IS BETTER THAN THE SWEETEST LIES</div>
  </section>

  <section class="welcome">
    <h1>Welcome To Brellwick</h1>
    <p>Lorem Ipsum is simply dummy text of the printing and typeset ting industry. Lorem Ipsum has been the industry's stan dard dummy text ever since the 1500s, when an unknown printer took a galley of type and scrambled it to make a type specimen book. It has survived not only five centuries. Lorem Ipsum is simply dummy text of the printing and typeset ting industry. Lorem Ipsum has been the industry's stan dard dummy text ever since the 1500s, when an unknown printer took a galley of type and scrambled it to make a type specimen book. It has survived not only five centuries</p>
  </section>

  <aside class="client-login">
    <h2>Client Login</h2>
    <div class="field">UserName</div>
    <div class="field">•••••••</div>
    <span class="btn">Login</span>
  </aside>

  <section class="info-panel">
    <div class="info-col col-do">
      <h3>WHAT WE DO</h3>
      <p>Harrowgate &amp; Associates' private investigators are available for immediate service in Ohio throughout the cities of Ironton, Portsmouth, Gallipolis, Jackson, Chillicothe, Cincinnati, Columbus, and surrounding areas. Service is immediately available in West Virginia throughout the cities of Huntington, Charleston, and surrounding areas.<br><br>Private investigators are available to provide full support to attorneys involved in criminal defense and civil litigation. Full investigative support is available to the general public involving criminal</p>
    </div>
    <span class="read-more rm-do">read more</span>
    <div class="info-col col-charge">
      <h3>HOW MUCH DO WE CHARGE</h3>
      <p>We believe the services of a private investigator should be obtainable and reasonable to the general public. The fees charged by Harrowgate &amp; Associates are low compared to other similar firms. For one, we do not charge for travel. This makes us available to you without unnecessary expense. Investigative and analysis services are available by the hour or at a flat rate. See the private investigator fees for more information.<br>Our investigative and analysis ability is based on the application of Structured Analysis and Expert Judgement. The use of these methods allows us to</p>
    </div>
    <span class="read-more rm-charge">read more</span>
    <div class="info-col col-clients">
      <h3>WHAT OUR CLIENTS SAY</h3>
      <p class="quote">"Our experience and unbiased approach is your greatest strength! If you are an attorney, company, or private individual with a legal need we will provide you with accurate, timely and unbiased information that will help you make an informed decision, mitigate risk, and</p>
      <p class="quote-author">DANA WHITLOW</p>
      <div class="consult">
        <div class="label">CALL FOR A FREE<br>CONSULTATION</div>
        <div class="phone">(555) 014-2276</div>
      </div>
    </div>
  </section>

  <footer class="site-footer">
    <div class="footer-nav">Home | About Us | Main | Investigations &amp; Analysis | News | Contacts</div>
    <div class="footer-social"><span></span><span></span><span></span><span></span></div>
    <div class="copyright"><b>Brellwick</b> © 2015 All rights reserved.</div>
  </footer>
</body>
</html>
```